Tampa Bay fishing guide needs stunning website.

I currently have a site - www.reelcoveguide.net which I personally put together using the Pagely platform and I am looking for a redesign on a different platform (Sitecraft?) that will allow me to easily create landing pages in the future. Would like to have a block for visitors to opt in to newsletter. Need social media links on all pages.

I would like to let my visitors know that I am able to handle their fishing charter needs here in the Tampa Bay area, if I'm not available for the dates they are looking to go I can refer them to a reputable captain in the area.

Target Market(s)

United States

Industry/Entity Type

Tourism

Coding

Coded - Design and coding required

Number of Pages Required

5+ page

Font styles to use
Sans Serif

Colors
0355a3
3176b5
85abd2
fbf289

Requirements
Must have
• Mobile Responsive, Ability to insert Vantor Metrics, Chatterbox pixels, ability to add custom landing pages in future
Nice to have
• Clean, easy navigation

```html
<!DOCTYPE html>
<html lang="en">
<head>
<meta charset="utf-8">
<title>Capt. Rhett Callahan – Tampa Bay Fishing Charters</title>
<link href="https://fonts.googleapis.com/css2?family=Roboto:wght@400;500;700&family=Open+Sans:wght@400;600&display=swap" rel="stylesheet">
<style>
:root{
  --blue:#1a6ad9;
  --blue-dark:#0355a3;
  --ink:#1c1c1c;
  --text:#555;
  --muted:#777;
  --line:#e2e2e2;
  --orange:#f57c00;
  --charcoal:#444;
  --white:#fff;
  --field:#ededed;
}
*{box-sizing:border-box;margin:0;padding:0}
html,body{width:1200px;height:2264px;overflow:hidden;background:var(--white)}
body{position:relative;font-family:"Roboto",sans-serif;color:var(--ink)}
.abs{position:absolute}
/* header */
.brand{left:98px;top:30px;display:flex;align-items:center;gap:10px;font:700 34px "Roboto",sans-serif;color:var(--blue)}
.brand-dot{width:14px;height:14px;border-radius:50%;background:var(--blue)}
.nav{left:496px;top:46px;font:400 13px "Roboto",sans-serif;color:#333;display:flex}
.nav a{position:absolute;white-space:nowrap;color:#333;text-decoration:none}
.nav a.active{color:var(--blue)}
/* hero */
.hero{left:0;top:101px;width:1200px;height:536px;background:linear-gradient(135deg,#0e1a22 0%,#24343d 35%,#c9d6e2 60%,#eef3f7 80%,#5d6a72 100%)}
.call{left:854px;top:101px;width:272px;height:45px;background:var(--blue);color:var(--white);font:400 14px "Roboto",sans-serif;display:flex;align-items:center}
.call .ico{width:38px;height:45px;background:var(--blue-dark);display:flex;align-items:center;justify-content:center;margin-right:11px}
.arrow{top:355px;width:32px;height:32px;border-radius:50%;background:rgba(60,60,60,.8);display:flex;align-items:center;justify-content:center}
.caption{left:98px;top:462px;width:418px;height:114px;background:rgba(20,20,20,.85);color:var(--white);font:400 19px/25px "Roboto",sans-serif;padding:17px 25px}
/* intro */
.intro-title{left:300px;top:683px;width:600px;text-align:center;font:500 26px/32px "Roboto",sans-serif;letter-spacing:1.5px}
.intro-text{left:106px;top:769px;width:988px;text-align:center;font:400 12px/20px "Open Sans",sans-serif;color:var(--text)}
.btn{height:39px;color:var(--white);font:400 13px "Roboto",sans-serif;display:flex;align-items:center;justify-content:center;gap:8px}
.btn-primary{background:var(--blue)}
.btn-dark{background:var(--charcoal)}
.btn-orange{background:var(--orange)}
.chev{width:15px;height:15px;border-radius:50%;background:var(--white);display:inline-flex;align-items:center;justify-content:center}
/* features */
.photo{display:block}
.feature h3{font:500 16px "Roboto",sans-serif;color:var(--ink);margin-bottom:14px}
.feature p{font:400 12px/20px "Open Sans",sans-serif;color:var(--text);width:270px}
.feature .more{margin-top:16px;font:400 12px "Open Sans",sans-serif;color:#444;display:flex;align-items:center;gap:10px}
.more .chev{background:#444}
/* band */
.band{left:0;top:1252px;width:1200px;height:215px;background:var(--blue);color:var(--white);text-align:center}
.band strong{display:block;font:700 19px "Roboto",sans-serif;margin-top:46px}
.band span{display:block;font:400 19px "Roboto",sans-serif;margin-top:14px}
/* gallery */
.gallery-title{left:0;top:1515px;width:1200px;text-align:center;font:500 24px "Roboto",sans-serif}
.dots{left:582px;top:1811px;display:flex;gap:5px}
.dots i{width:6px;height:6px;border-radius:50%;background:#ccc}
.dots i.on{background:var(--blue)}
/* footer */
.rule{left:0;width:1200px;height:1px;background:var(--line)}
.foot-h{top:1926px;font:600 14px "Open Sans",sans-serif;letter-spacing:.5px;color:#222}
.pickups{left:98px;top:1973px;list-style:none;font:400 12px "Open Sans",sans-serif;color:var(--muted)}
.pickups li{height:30.5px;display:flex;align-items:flex-start;gap:18px}
.pickups li::before{content:"";width:5px;height:5px;border-radius:50%;background:var(--blue);margin-top:6px}
.contact{left:353px;font:400 12px/19px "Open Sans",sans-serif;color:var(--muted);display:flex;gap:18px}
.social{left:358px;top:2132px;display:flex;gap:20px}
.social i{width:15px;height:15px;border-radius:3px;background:#888}
.field{left:647px;top:1972px;width:273px;height:35px;background:var(--field);font:400 12px "Open Sans",sans-serif;color:#666;padding:11px 14px}
.subscribe{left:927px;top:1972px;width:175px;height:35px;background:var(--blue);color:var(--white);font:600 14px "Open Sans",sans-serif;display:flex;align-items:center;justify-content:center}
.copy{left:0;top:2223px;width:1200px;text-align:center;font:400 11px "Open Sans",sans-serif;color:#666}
</style>
</head>
<body>

<header>
  <div class="abs brand"><span class="brand-dot"></span>Callahan</div>
  <nav class="abs nav">
    <a class="active" style="left:0">HOME</a>
    <a style="left:76px">ABOUT US</a>
    <a style="left:179px">PICK UP LOCATIONS</a>
    <a style="left:342px">RATES</a>
    <a style="left:420px">CONTACT US</a>
    <a style="left:539px">GIFT CARD</a>
  </nav>
</header>

<section>
  <div class="abs hero" role="img" aria-label="Smiling angler on a boat deck holding a rod while a leaping tarpon splashes beside the boat"></div>
  <div class="abs call"><span class="ico"><svg width="16" height="16" viewBox="0 0 24 24"><path fill="#fff" d="M6.6 10.8a15 15 0 0 0 6.6 6.6l2.2-2.2c.3-.3.7-.4 1-.2 1.1.4 2.3.6 3.6.6.6 0 1 .4 1 1V20c0 .6-.4 1-1 1A17 17 0 0 1 3 4c0-.6.4-1 1-1h3.5c.6 0 1 .4 1 1 0 1.3.2 2.5.6 3.6.1.3 0 .7-.2 1z"/></svg></span>CALL CAPT. RHETT (555) 014-2287</div>
  <div class="abs arrow" style="left:14px"><svg width="12" height="12" viewBox="0 0 12 12"><path d="M8 1 3 6l5 5" stroke="#111" stroke-width="2" fill="none"/></svg></div>
  <div class="abs arrow" style="left:1154px"><svg width="12" height="12" viewBox="0 0 12 12"><path d="m4 1 5 5-5 5" stroke="#111" stroke-width="2" fill="none"/></svg></div>
  <div class="abs caption">Come fish with Tampa Bay, FL fishing guide, Tampa Bay fishing charter most respected Captain, 25 year Native Guide</div>
</section>

<section>
  <h1 class="abs intro-title">TAMPABAY,FISHINGGUIDE,TAMPABAY FISHINGCHARTERS</h1>
  <p class="abs intro-text">Capt. Rhett Callahan, with over 20 years' experience, Native fishing charter tampa charter captain offering full and half day fishing charters on the waters of Tampa Bay.<br>If you're looking for a great fishing charter tampa don't hesitate to contact Capt. Rhett or you can simply book your trip online here. Come enjoy a wonderful day fishing charters Tampa for Tarpon, Snook, Redfish, Trout, Sharks, Cobia, Spanish mackerel as well as others aboard Capt. Rhett Callahan Sport fishing Charters boat. Capt. Rhett will work hard to ensure that you and your guests have a memorable day enjoying the wonderful gamefish that Tampa Bay has to offer.</p>
  <div class="abs btn btn-primary" style="left:465px;top:881px;width:131px">Read More <span class="chev"><svg width="7" height="7" viewBox="0 0 8 8"><path d="m2 1 3 3-3 3" stroke="#1a6ad9" stroke-width="1.6" fill="none"/></svg></span></div>
  <div class="abs btn btn-dark" style="left:602px;top:881px;width:131px">Contact Us <span class="chev"><svg width="7" height="7" viewBox="0 0 8 8"><path d="m2 1 3 3-3 3" stroke="#444" stroke-width="1.6" fill="none"/></svg></span></div>
</section>

<section>
  <div class="abs photo" style="left:98px;top:996px;width:196px;height:181px;background:linear-gradient(160deg,#cfe0ee,#8aa7bb 55%,#c85a4a)" role="img" aria-label="Two anglers on a boat holding a large snook"></div>
  <div class="abs feature" style="left:321px;top:994px">
    <h3>FULL &amp; HALF DAY CHARTERS</h3>
    <p>Offering Tampa Bay, FL fishing charters on the beautiful waters of Tampa Bay. Fish with Capt. Rhett Callahan, Tampa Bay, FL fishing guide for over 20 years</p>
    <div class="more">Find Out More <span class="chev"><svg width="7" height="7" viewBox="0 0 8 8"><path d="m2 1 3 3-3 3" stroke="#fff" stroke-width="1.6" fill="none"/></svg></span></div>
  </div>
  <div class="abs photo" style="left:613px;top:996px;width:196px;height:181px;background:linear-gradient(180deg,#3a4a82 0%,#b77aa0 35%,#f2a65a 50%,#6e7fa8 65%,#2a3550 100%)" role="img" aria-label="Wooden pier stretching into calm water at sunset"></div>
  <div class="abs feature" style="left:836px;top:994px">
    <h3>MULTIPLE PICKUP POINTS</h3>
    <p>Whether you're looking for a fishing charter/guide in Tampa, St. Pete, Clearwater or Bradenton, Capt. Rhett can pick you up nearby. Click here for maps of pickup locations.</p>
    <div class="more">Maps &amp; pickup locations <span class="chev"><svg width="7" height="7" viewBox="0 0 8 8"><path d="m2 1 3 3-3 3" stroke="#fff" stroke-width="1.6" fill="none"/></svg></span></div>
  </div>
</section>

<section class="abs band">
  <strong>I am able to handle your fishing charter needs here in the Tampa Bay area.</strong>
  <span>If I'm not available for the dates they are looking to go I can refer you to a reputable captain in the area.</span>
  <div class="abs btn btn-orange" style="left:542px;top:130px;width:133px;height:40px">More Details <span class="chev"><svg width="7" height="7" viewBox="0 0 8 8"><path d="m2 1 3 3-3 3" stroke="#f57c00" stroke-width="1.6" fill="none"/></svg></span></div>
</section>

<section>
  <h2 class="abs gallery-title">OUR GALLERY</h2>
  <div class="abs photo" style="left:98px;top:1580px;width:238px;height:190px;background:linear-gradient(135deg,#1f6b55,#3f8f73 55%,#e7ecef)" role="img" aria-label="Anglers landing a snook beside the boat"></div>
  <div class="abs photo" style="left:353px;top:1580px;width:239px;height:190px;background:linear-gradient(180deg,#8fc0e8,#5f9fc6 45%,#2f6f8f)" role="img" aria-label="Angler standing in the bay holding a snook"></div>
  <div class="abs photo" style="left:608px;top:1580px;width:239px;height:190px;background:linear-gradient(180deg,#e9e4dc,#cfc6b8 60%,#8e8a80)" role="img" aria-label="Fisherman releasing a tarpon over the side of the boat"></div>
  <div class="abs photo" style="left:863px;top:1580px;width:239px;height:190px;background:linear-gradient(180deg,#cfe2f3,#b6c7a6 55%,#6d7a62)" role="img" aria-label="Two anglers fishing from the boat with rods"></div>
  <div class="abs dots"><i class="on"></i><i></i><i></i><i></i></div>
</section>

<footer>
  <div class="abs rule" style="top:1874px"></div>
  <h4 class="abs foot-h" style="left:98px">PICKUP LOCATIONS</h4>
  <h4 class="abs foot-h" style="left:353px">CONTACT INFO</h4>
  <h4 class="abs foot-h" style="left:644px">NEWSLETTER SIGNUP</h4>
  <ul class="abs pickups">
    <li>Bayview Marina - St. Petersburg</li>
    <li>Palm Cove - Ruskin</li>
    <li>Causeway Boat Ramp</li>
    <li>Sandpiper Boat Ramp</li>
  </ul>
  <div class="abs contact" style="top:1974px"><svg width="13" height="13" viewBox="0 0 14 14"><rect x="1" y="3" width="12" height="8" fill="none" stroke="#777" stroke-width="1.2"/><path d="m1 3 6 5 6-5" fill="none" stroke="#777" stroke-width="1.2"/></svg>captain@reelcoveguide.net</div>
  <div class="abs contact" style="top:2017px"><svg width="13" height="13" viewBox="0 0 24 24"><path fill="#777" d="M6.6 10.8a15 15 0 0 0 6.6 6.6l2.2-2.2c.3-.3.7-.4 1-.2 1.1.4 2.3.6 3.6.6.6 0 1 .4 1 1V20c0 .6-.4 1-1 1A17 17 0 0 1 3 4c0-.6.4-1 1-1h3.5c.6 0 1 .4 1 1 0 1.3.2 2.5.6 3.6.1.3 0 .7-.2 1z"/></svg>555-014-2287</div>
  <div class="abs contact" style="top:2069px"><svg width="13" height="14" viewBox="0 0 12 16"><path fill="#777" d="M6 0a6 6 0 0 0-6 6c0 4.5 6 10 6 10s6-5.5 6-10a6 6 0 0 0-6-6zm0 8.5A2.5 2.5 0 1 1 6 3.5a2.5 2.5 0 0 1 0 5z"/></svg><span>410 Harbor Lane. Suite 12<br>Seabrook, FL 30000</span></div>
  <div class="abs social" aria-label="Social media links"><i></i><i></i><i></i><i></i><i></i><i></i></div>
  <div class="abs field">Email Id</div>
  <div class="abs subscribe">SUBSCRIBE</div>
  <div class="abs" style="left:649px;top:2034px;width:97px;height:82px;background:#dfe8f4;border:2px solid #2c5fa8" role="img" aria-label="Angler review badge"></div>
  <div class="abs" style="left:763px;top:2034px;width:98px;height:70px;background:#eef4e8;border-top:18px solid #4a8a3a" role="img" aria-label="Traveler rating badge"></div>
  <div class="abs" style="left:878px;top:2036px;width:50px;height:30px;background:#1c4fa0" role="img" aria-label="Debit card accepted"></div>
  <div class="abs" style="left:937px;top:2036px;width:50px;height:30px;background:#f2f2f2;border:1px solid #ccc" role="img" aria-label="Credit card accepted"></div>
  <div class="abs" style="left:878px;top:2080px;width:50px;height:30px;background:#fbe9c8;border:1px solid #e0a040" role="img" aria-label="Online payment accepted"></div>
  <div class="abs" style="left:937px;top:2080px;width:50px;height:30px;background:#1d2f6b" role="img" aria-label="Card payment accepted"></div>
  <div class="abs rule" style="top:2197px;left:100px;width:1000px"></div>
  <p class="abs copy">Copyright © 2016 - yoursite, All Rights Reserved</p>
</footer>

</body>
</html>
```